I need a sophisticated and powerful book cover design that combines Japanese minimalism with contemporary appeal. The cover should convey personal transformation through the metaphor of a katana (Japanese sword).
Key Design Elements:
A katana, either partially shown or artistically rendered
Subtle Japanese design elements without being stereotypical
Clean, minimalist aesthetic
Professional font selection that bridges Eastern and Western typography
Color scheme: Deep blacks, steel grays, and possibly a touch of red or gold for accent
Mood/Style:
Professional and sophisticated
Blend of traditional Japanese aesthetics with modern design
Should appeal to personal development and business readers
Must convey strength and transformation
Elegant rather than aggressive
Specific Requirements:
Title: "The Lantern Compass"
Subtitle: "Quiet Methods for Growing Inner Steadiness and Calm Endurance"
Author names: Dorvelan Thaske and Meloda Thaske
Cover dimensions: Standard hardcover book size (6" x 9")
Must work well in both physical and digital thumbnail formats
Should be striking and legible when viewed as a small image online
Design Specifics:
Japanese elements such as brushstroke effects, kanji characters, or wave patterns
The design should reflect the book's core message: personal transformation through Japanese wisdom principles, using the katana as a metaphor for growth and development.

```html
<!DOCTYPE html>
<html lang="en">
<head>
<meta charset="utf-8">
<title>The Lantern Compass — Book Cover</title>
<link rel="stylesheet" href="https://fonts.googleapis.com/css2?family=Montserrat:wght@400;500;800;900&display=swap">
<style>
  :root {
    --backdrop: #000000;
    --paper: #ffffff;
    --sun-red: #ec1c24;
    --sun-deep: #b8141a;
    --title-red: #ea2628;
    --ink: #111111;
    --steel-light: #e6e9ee;
    --steel-dark: #5c636e;
    --blossom: #f4b6c4;
  }
  html, body {
    margin: 0;
    width: 1200px;
    height: 1200px;
    overflow: hidden;
    background: var(--backdrop);
  }
  .cover {
    position: absolute;
    left: 240px;
    top: 60px;
    width: 720px;
    height: 1080px;
    background: var(--paper);
    overflow: hidden;
    font-family: "Montserrat", sans-serif;
  }
  .artwork {
    position: absolute;
    left: 0;
    top: 0;
    width: 720px;
    height: 1080px;
  }
  .title { margin: 0; }
  .title-block {
    position: absolute;
    left: 0;
    width: 720px;
    text-align: center;
    font-weight: 800;
    line-height: 1;
  }
  .title-lead {
    top: 552px;
    font-size: 78px;
    font-weight: 900;
    letter-spacing: 5px;
    color: var(--ink);
  }
  .title-main {
    font-size: 106px;
    color: var(--title-red);
    letter-spacing: 1px;
  }
  .title-main.line-one { top: 626px; }
  .title-main.line-two { top: 728px; }
  .subtitle {
    position: absolute;
    left: 90px;
    width: 540px;
    top: 848px;
    margin: 0;
    text-align: center;
    font-size: 27px;
    font-weight: 500;
    line-height: 35px;
    color: var(--ink);
    letter-spacing: 0.5px;
  }
  .authors {
    position: absolute;
    left: 0;
    width: 720px;
    top: 982px;
    margin: 0;
    text-align: center;
    font-size: 36px;
    font-weight: 500;
    color: var(--ink);
  }
</style>
</head>
<body>
  <main class="cover">
    <svg class="artwork" viewBox="0 0 720 1080" xmlns="http://www.w3.org/2000/svg">
      <defs>
        <radialGradient id="sun-fill" cx="0.42" cy="0.38" r="0.7">
          <stop offset="0" stop-color="#f14a4c"/>
          <stop offset="0.55" stop-color="#ec1c24"/>
          <stop offset="1" stop-color="#b8141a"/>
        </radialGradient>
        <linearGradient id="sword-fill" x1="0" x2="0" y1="0" y2="1">
          <stop offset="0" stop-color="#1c1f27"/>
          <stop offset="0.28" stop-color="#5c636e"/>
          <stop offset="0.5" stop-color="#e6e9ee"/>
          <stop offset="1" stop-color="#b7bcc5"/>
        </linearGradient>
        <linearGradient id="blossom-fill" x1="0" y1="0" x2="1" y2="0">
          <stop offset="0" stop-color="#f4b6c4" stop-opacity="0.75"/>
          <stop offset="1" stop-color="#f4b6c4" stop-opacity="0.25"/>
        </linearGradient>
      </defs>
      <g class="blossom-branch" role="img" aria-label="Cherry blossom branch reaching in from the top-left corner">
        <rect x="-10" y="-14" width="175" height="34" rx="17" fill="url(#blossom-fill)" transform="rotate(38)"/>
      </g>
      <g class="brush-sun" role="img" aria-label="Red brushstroke sun disc">
        <circle cx="360" cy="352" r="300" fill="url(#sun-fill)"/>
      </g>
      <g class="sword" role="img" aria-label="Upright katana with dark wrapped hilt, gold guard and polished steel blade">
        <rect x="342" y="16" width="36" height="822" fill="url(#sword-fill)"/>
      </g>
    </svg>

    <h1 class="title">
      <span class="title-block title-lead">THE</span>
      <span class="title-block title-main line-one">LANTERN</span>
      <span class="title-block title-main line-two">COMPASS</span>
    </h1>

    <p class="subtitle">Quiet Methods for Growing Inner Steadiness and Calm Endurance</p>

    <p class="authors">Dorvelan Thaske &amp; Meloda Thaske</p>
  </main>
</body>
</html>
```